Brindle Asset Management Vendor Recruiting Email

We need a digital flyer to email and post on Social media to attract new vendors to our website to apply to complete maintenance work on our clients homes. I have one flyer we had produced recently that we are un-happy with. It is attached.

The example given is what we do not want!! We do not want any of the pictures used from the existing one

Target Market(s)

Construction companies and handyman

Industry/Entity Type

Residential maintenance and repairs

Requirements
Must have
• Join our team as the header not become a vendor

```html
<!DOCTYPE html>
<html lang="en">
<head>
<meta charset="utf-8">
<title>Brindle Asset Management – Join Our Team</title>
<link rel="stylesheet" href="https://fonts.googleapis.com/css2?family=Montserrat:wght@600;800;900&family=Marcellus&display=swap">
<style>
  :root {
    --ink: #0b0a12;
    --navy: #120f22;
    --purple: #6a2d96;
    --panel-top: #6a6a9c;
    --panel-bottom: #8886c4;
    --white: #ffffff;
    --grey-text: #2e2e36;
    --yellow: #f6b80a;
    --sky: #a9c8ea;
    --grass: #5c9a3a;
  }
  * { box-sizing: border-box; margin: 0; padding: 0; }
  html, body { width: 1200px; height: 1200px; overflow: hidden; background: var(--white); }
  .flyer { position: relative; width: 1200px; height: 1200px; overflow: hidden; background: var(--white); font-family: "Marcellus", serif; }

  .hero-photo {
    position: absolute; left: 0; top: 0; width: 1200px; height: 727px;
    background:
      linear-gradient(90deg, rgba(0,0,0,0) 58%, rgba(40,44,80,0.55) 72%, rgba(40,44,80,0.7) 100%),
      linear-gradient(180deg, #8fb6e4 0%, var(--sky) 38%, #c9d6e2 60%, #8ca77a 80%, var(--grass) 100%);
  }

  .brand-box {
    position: absolute; left: 186px; top: 0; width: 303px; height: 167px;
    background: var(--navy); border-radius: 0 0 14px 14px;
    display: flex; align-items: center; justify-content: center; gap: 10px;
  }
  .brand-mark { width: 14px; height: 14px; background: var(--white); }
  .brand-name { font-family: "Montserrat", sans-serif; font-weight: 800; color: var(--white); font-size: 19px; line-height: 1.15; letter-spacing: 1px; }

  .headline { position: absolute; left: 81px; top: 232px; font-family: "Montserrat", sans-serif; font-weight: 800; line-height: 1; }
  .headline-top { display: block; font-size: 80px; color: var(--ink); margin-left: 23px; letter-spacing: 1px; }
  .headline-main { display: block; font-size: 102px; color: var(--purple); margin-top: 10px; letter-spacing: -1px;
    text-shadow: 3px 3px 0 var(--white), -2px -2px 0 var(--white), 2px -2px 0 var(--white), -2px 2px 0 var(--white); }

  .info-band { position: absolute; left: 0; top: 727px; width: 1200px; height: 473px; background: var(--white); border-top: 7px solid var(--purple); }
  .footer-strip { position: absolute; left: 0; bottom: 0; width: 1200px; height: 18px; background: var(--purple); }

  .panel-frame { position: absolute; left: 44px; top: 462px; width: 625px; height: 738px; background: var(--white); border-radius: 0 52px 0 0; }
  .benefit-panel {
    position: absolute; left: 54px; top: 473px; width: 605px; height: 727px;
    background: linear-gradient(180deg, var(--panel-top), var(--panel-bottom));
    border-radius: 0 44px 0 0;
  }

  .benefit-list { position: absolute; left: 24px; top: 42px; list-style: none; }
  .benefit-list li { position: relative; padding-left: 52px; color: var(--white); font-size: 29px; line-height: 40px; width: 482px;
    -webkit-text-stroke: 0.9px var(--white); letter-spacing: 0.3px; }
  .benefit-list li + li { margin-top: 38px; }
  .tick { position: absolute; left: 0; top: 7px; width: 26px; height: 26px; }

  .contact-tab { position: absolute; left: 177px; top: 938px; width: 145px; height: 40px; background: var(--purple); color: var(--white);
    font-family: "Montserrat", sans-serif; font-weight: 800; font-size: 22px; display: flex; align-items: center; justify-content: center;
    border-radius: 6px 6px 0 0; transform: rotate(-3deg); letter-spacing: 1px; }
  .phone-box { position: absolute; left: 100px; top: 966px; width: 494px; height: 122px; background: var(--white); border: 3px solid var(--ink);
    border-radius: 10px; transform: rotate(-3deg); display: flex; align-items: center; justify-content: center;
    font-family: "Montserrat", sans-serif; font-weight: 900; font-size: 68px; color: var(--ink); letter-spacing: -2px; }

  .web-bar { position: absolute; left: 76px; top: 1136px; width: 553px; height: 64px; background: var(--yellow); border-radius: 16px 16px 0 0;
    display: flex; align-items: center; justify-content: center; font-size: 30px; font-style: italic; color: var(--ink); -webkit-text-stroke: 0.4px var(--ink); }

  .req-title { position: absolute; left: 699px; top: 760px; font-family: "Montserrat", sans-serif; font-weight: 800; font-size: 35px; line-height: 44px; color: var(--purple); letter-spacing: -0.5px; }
  .req-list { position: absolute; left: 699px; top: 870px; list-style: none; }
  .req-list li { position: relative; padding-left: 54px; color: var(--grey-text); font-size: 27px; line-height: 29px; width: 480px; }
  .req-list li + li { margin-top: 26px; }
  .req-list .tick { top: 4px; width: 24px; height: 24px; }
</style>
</head>
<body>
<main class="flyer">
  <div class="hero-photo" role="img" aria-label="Tradesman in navy coveralls with clipboard and tool belt in front of a house on a lawn under blue sky"></div>

  <div class="brand-box">
    <span class="brand-mark"></span>
    <span class="brand-name">BRINDLE<br>ASSET MANAGEMENT</span>
  </div>

  <h1 class="headline">
    <span class="headline-top">JOIN</span>
    <span class="headline-main">OUR TEAM</span>
  </h1>

  <div class="info-band"></div>
  <div class="footer-strip"></div>

  <div class="panel-frame"></div>
  <section class="benefit-panel">
    <ul class="benefit-list">
      <li><svg class="tick" viewBox="0 0 26 26"><rect x="2" y="6" width="18" height="18" fill="none" stroke="#fff" stroke-width="2.5"/><path d="M6 14l5 5L24 3" fill="none" stroke="#000" stroke-width="4"/></svg>95% approval rating on all submitted climates.</li>
      <li><svg class="tick" viewBox="0 0 26 26"><rect x="2" y="6" width="18" height="18" fill="none" stroke="#fff" stroke-width="2.5"/><path d="M6 14l5 5L24 3" fill="none" stroke="#000" stroke-width="4"/></svg>Guaranteed work volume.</li>
      <li><svg class="tick" viewBox="0 0 26 26"><rect x="2" y="6" width="18" height="18" fill="none" stroke="#fff" stroke-width="2.5"/><path d="M6 14l5 5L24 3" fill="none" stroke="#000" stroke-width="4"/></svg>Material purchasing program to help vendors</li>
      <li><svg class="tick" viewBox="0 0 26 26"><rect x="2" y="6" width="18" height="18" fill="none" stroke="#fff" stroke-width="2.5"/><path d="M6 14l5 5L24 3" fill="none" stroke="#000" stroke-width="4"/></svg>Weekly secure direct deposit with net 30 payment terms</li>
    </ul>
  </section>

  <div class="contact-tab">CONTACT</div>
  <div class="phone-box">555-014-2290</div>
  <div class="web-bar">www.brindleassetgroup.com</div>

  <h2 class="req-title">REQUIREMENTS TO<br>BECOME A VENDOR</h2>
  <ul class="req-list">
    <li><svg class="tick" viewBox="0 0 26 26"><rect x="2" y="6" width="18" height="18" fill="none" stroke="#222" stroke-width="2"/><path d="M6 14l5 5L24 3" fill="none" stroke="#000" stroke-width="3.5"/></svg>Auto insurance</li>
    <li><svg class="tick" viewBox="0 0 26 26"><rect x="2" y="6" width="18" height="18" fill="none" stroke="#222" stroke-width="2"/><path d="M6 14l5 5L24 3" fill="none" stroke="#000" stroke-width="3.5"/></svg>Certificate of general liability insurance</li>
    <li><svg class="tick" viewBox="0 0 26 26"><rect x="2" y="6" width="18" height="18" fill="none" stroke="#222" stroke-width="2"/><path d="M6 14l5 5L24 3" fill="none" stroke="#000" stroke-width="3.5"/></svg>Workman’s Compensation or state issued exemption letter</li>
    <li><svg class="tick" viewBox="0 0 26 26"><rect x="2" y="6" width="18" height="18" fill="none" stroke="#222" stroke-width="2"/><path d="M6 14l5 5L24 3" fill="none" stroke="#000" stroke-width="3.5"/></svg>Coverage area</li>
    <li><svg class="tick" viewBox="0 0 26 26"><rect x="2" y="6" width="18" height="18" fill="none" stroke="#222" stroke-width="2"/><path d="M6 14l5 5L24 3" fill="none" stroke="#000" stroke-width="3.5"/></svg>Any speciality Licenses</li>
  </ul>
</main>
</body>
</html>
```